Need Business Card for our Real Estate Business with Sales Executive's Picture

PANTONE 484 C ( RED)

PANTONE 2766 C ( BLUE

Industry/Entity Type

Real Estate

Contact Information for Business Card

Name, Mobile, email, & picture of Person
Agency Phone, address, Web address

Requirements
Must have
• Our Logo Colours, Agent Picture,

```html
<!DOCTYPE html>
<html lang="en">
<head>
<meta charset="utf-8">
<title>Meridian Real Estate – Business Card</title>
<link href="https://fonts.googleapis.com/css2?family=Lato:wght@400;700&display=swap" rel="stylesheet">
<style>
  :root {
    --navy: #262a40;
    --red: #6b2326;
    --white: #ffffff;
    --suit-blue: #2a4a9a;
    --backdrop: #5e5e5e;
    --text-light: #f2f2f5;
  }
  * { box-sizing: border-box; margin: 0; padding: 0; }
  html, body { width: 1200px; height: 1200px; overflow: hidden; }
  body {
    background: var(--backdrop);
    font-family: "Lato", sans-serif;
    position: relative;
  }
  .card {
    position: absolute;
    left: 150px;
    width: 900px;
    height: 514px;
    overflow: hidden;
    background: var(--navy);
  }
  .card--brand { top: 50px; }
  .card--contact { top: 618px; }

  /* Brand side */
  .brand {
    position: absolute;
    inset: 0;
    display: flex;
    flex-direction: column;
    align-items: center;
    justify-content: center;
    color: var(--white);
  }
  .brand__name {
    display: flex;
    align-items: center;
    gap: 18px;
    font-weight: 700;
    font-size: 58px;
    letter-spacing: 6px;
    text-transform: uppercase;
  }
  .brand__mark {
    width: 22px;
    height: 22px;
    background: var(--red);
  }
  .brand__web {
    margin-top: 60px;
    font-size: 24px;
    letter-spacing: 2px;
  }

  /* Contact side */
  .contact__shapes { position: absolute; inset: 0; }
  .contact__photo {
    position: absolute;
    left: 705px;
    top: 30px;
    width: 195px;
    height: 484px;
    background: linear-gradient(180deg, var(--white) 0%, #e9ecf4 35%, #6f86c2 65%, var(--suit-blue) 100%);
  }
  .contact__info {
    position: absolute;
    left: 80px;
    top: 80px;
    color: var(--text-light);
  }
  .contact__name {
    color: var(--red);
    font-weight: 700;
    font-size: 38px;
    text-transform: uppercase;
    letter-spacing: 0.5px;
  }
  .contact__role { font-size: 25px; margin-top: 4px; }
  .contact__list { list-style: none; margin-top: 26px; }
  .contact__list li {
    display: flex;
    align-items: center;
    gap: 24px;
    font-size: 25px;
    line-height: 32px;
  }
  .contact__list svg { width: 20px; height: 20px; flex: none; }
  .contact__address { margin-top: 24px; font-size: 27px; line-height: 34px; }
</style>
</head>
<body>

<section class="card card--brand" aria-label="Card front">
  <div class="brand">
    <div class="brand__name"><span class="brand__mark"></span>Meridian Real Estate</div>
    <div class="brand__web">www.meridianhomes.com</div>
  </div>
</section>

<section class="card card--contact" aria-label="Card back">
  <svg class="contact__shapes" viewBox="0 0 900 514" preserveAspectRatio="none">
    <path d="M690,0 Q600,330 350,514 L900,514 L900,0 Z" fill="var(--white)"/>
    <path d="M690,0 Q600,330 350,514" fill="none" stroke="var(--red)" stroke-width="10"/>
    <path d="M0,470 Q300,450 540,250 Q380,470 0,514 Z" fill="var(--red)"/>
  </svg>
  <div class="contact__photo" role="img" aria-label="Portrait photo of the sales executive"></div>
  <div class="contact__info">
    <h1 class="contact__name">Daniel Hartley</h1>
    <p class="contact__role">Manager</p>
    <ul class="contact__list">
      <li><svg viewBox="0 0 20 20"><path d="M4 2l4 1 1 4-2 2a11 11 0 0 0 4 4l2-2 4 1 1 4-2 2C8 18 2 12 2 4z" fill="var(--red)"/></svg>512 555 0140</li>
      <li><svg viewBox="0 0 20 20"><rect x="5" y="1" width="10" height="18" rx="2" fill="var(--red)"/><rect x="7" y="4" width="6" height="10" fill="var(--navy)"/></svg>512 555 0141</li>
      <li><svg viewBox="0 0 20 20"><rect x="1" y="4" width="18" height="12" fill="var(--red)"/><path d="M1 4l9 7 9-7" fill="none" stroke="var(--navy)" stroke-width="1.5"/></svg>info@meridianhomes.com</li>
      <li><svg viewBox="0 0 20 20"><circle cx="10" cy="10" r="9" fill="var(--red)"/><path d="M1 10h18M10 1v18M4 4q6 4 12 0M4 16q6-4 12 0" fill="none" stroke="var(--navy)" stroke-width="1"/></svg>www.meridianhomes.com</li>
    </ul>
    <p class="contact__address">418 Cedar Row<br>Houston, TX 77001</p>
  </div>
</section>

</body>
</html>
```